Label Design for 2x Chutney Products

We need a label design for 2x Chutney Products.
Marigo Chutney - Red Chili
Marigo Chutney - Green Chili & Coriander
See attached pictures. This is just sample pictures so you get an impression of the product and the colors. Both labels to have as title the generic name "Marigo Chutney" and then added either Red Chili or Green Chili & Coriander. The different terms needs to be good readable and can differ in font/color/size, or in the same style if this makes more sense from design point (as I am not a designer). The labels later on need to be editable in the way that the ingredient list, nutrition list, basis company and production information can be added. If this needs to be done directly and cannot be edited later on please let know. Editable design related the additional text also would be good as the additional information need to be added in different languages (Dutch. German and perhaps French). No clue how this is to be implemented but looking forward to receive some input/solutions on this.
I already had a project to create the company logo. I consider this logo to be used as the product logo and not the company logo. A different company logo later on can be designed from new. This logo is here attached. Either to work with this logo and use it as product logo (perhaps revise the colors) and add the product description or create a new logo for the product from scratch if you feel too. The logo itself should be easily readable for the product name/description and the colors appealing to such product and of course customers.
Please contact if any clarification needed. Thanks in advance for your efforts and ideas for this project.

Industry/Entity Type

Food

Font styles to use
Other font styles liked:
• Asian Touch

Requirements
Nice to have
• If possible "simply" editable for text fields in order to add/revise the ingredient list, nutrition list, revise to different languages.

```html
<!DOCTYPE html>
<html lang="en">
<head>
<meta charset="utf-8">
<title>Marigo Chutney – Red Chili Label</title>
<link href="https://fonts.googleapis.com/css2?family=Graduate&family=Montserrat:wght@600&family=Yellowtail&display=swap" rel="stylesheet">
<style>
  :root {
    --backdrop: #e8e8e9;
    --label-dark: #3b2a22;
    --label-dark-edge: #241813;
    --chili-red: #c8221f;
    --chili-red-deep: #a81a18;
    --ribbon-white: #eeeeee;
    --ribbon-shade: #d3d3d3;
    --type-light: #f1f1f1;
    --type-cream: #f6e7dc;
    --brand-grey: #4a4a4a;
    --brand-dot: #5c9a2f;
  }
  html, body {
    margin: 0;
    padding: 0;
    width: 1200px;
    height: 1200px;
    overflow: hidden;
    background: var(--backdrop);
  }
  .canvas {
    position: relative;
    width: 1200px;
    height: 1200px;
  }
  .label {
    position: absolute;
    left: 100px;
    top: 300px;
    width: 1000px;
    height: 600px;
    overflow: hidden;
    background: radial-gradient(ellipse at 60% 40%, var(--label-dark) 0%, var(--label-dark-edge) 100%);
    box-shadow: 0 10px 30px rgba(0,0,0,0.18);
  }
  .brush-band {
    position: absolute;
    inset: 0;
    width: 100%;
    height: 100%;
  }
  .brand-ribbon {
    position: absolute;
    left: 440px;
    top: 0;
    width: 120px;
    height: 190px;
  }
  .brand-ribbon svg {
    position: absolute;
    inset: 0;
  }
  .brand-mark {
    position: absolute;
    top: 38px;
    left: 0;
    width: 120px;
    display: flex;
    flex-direction: column;
    align-items: center;
    gap: 10px;
  }
  .brand-dot {
    width: 44px;
    height: 44px;
    border-radius: 50%;
    background: var(--brand-dot);
  }
  .brand-name {
    font-family: "Montserrat", sans-serif;
    font-weight: 600;
    font-size: 19px;
    line-height: 1.05;
    text-align: center;
    color: var(--brand-grey);
    letter-spacing: 0.5px;
  }
  .product-title {
    position: absolute;
    top: 215px;
    left: 0;
    width: 100%;
    margin: 0;
    text-align: center;
    font-family: "Graduate", serif;
    font-weight: 400;
    font-size: 92px;
    line-height: 0.98;
    color: var(--type-light);
    letter-spacing: 1px;
    text-shadow: 0 3px 6px rgba(0,0,0,0.25);
  }
  .chili-illustration {
    position: absolute;
    left: 290px;
    top: 420px;
    width: 250px;
    height: 130px;
  }
  .flavour-name {
    position: absolute;
    left: 600px;
    top: 440px;
    margin: 0;
    font-family: "Yellowtail", cursive;
    font-size: 46px;
    font-weight: 400;
    color: var(--type-cream);
  }
</style>
</head>
<body>
<main class="canvas">
  <section class="label">
    <svg class="brush-band" viewBox="0 0 1000 600" preserveAspectRatio="none" aria-hidden="true">
      <polygon fill="var(--chili-red)" points="0,600 0,470 60,430 40,410 130,360 110,340 240,270 215,250 360,185 340,165 470,110 560,95 700,60 690,85 820,40 800,75 900,55 870,95 1000,70 1000,600"/>
      <polygon fill="var(--chili-red-deep)" opacity="0.35" points="0,600 1000,600 1000,420 600,560"/>
    </svg>

    <div class="brand-ribbon">
      <svg viewBox="0 0 120 190" width="120" height="190" aria-hidden="true">
        <polygon fill="var(--ribbon-white)" points="0,0 120,0 120,190 60,160 0,190"/>
        <polygon fill="var(--ribbon-shade)" points="0,0 8,0 8,186 0,190"/>
      </svg>
      <div class="brand-mark">
        <span class="brand-dot"></span>
        <span class="brand-name">KESARI<br>FOODS</span>
      </div>
    </div>

    <h1 class="product-title">MARIGO<br>CHUTNEY</h1>

    <svg class="chili-illustration" role="img" aria-label="Illustration of three fresh red chili peppers" viewBox="0 0 250 130">
      <defs>
        <linearGradient id="chili-tone" x1="0" y1="0" x2="1" y2="1">
          <stop offset="0" stop-color="#d8302a"/>
          <stop offset="1" stop-color="#8e1210"/>
        </linearGradient>
      </defs>
      <rect width="250" height="130" rx="20" fill="url(#chili-tone)" opacity="0.85"/>
    </svg>

    <p class="flavour-name">Red Chili</p>
  </section>
</main>
</body>
</html>
```